Business Card Design

New business card design

Target Market(s)

Residential & Commercial Property Managers

Industry/Entity Type

Plumbing Services

Contact Information for Business Card

Name - Rowan Keddle, title - Director, Phone Number - 0431 286 517, email - rowan@tbk-plumbing.com.au, Company ABN - 73 215 904 386,

Font styles to use
Sans Serif

Colors
0054AA
0677BA
7BADD7
CADEEF
E8F1F8

```html
<!DOCTYPE html>
<html lang="en">
<head>
<meta charset="utf-8">
<title>TBK Plumbing Services – Business Card</title>
<link rel="stylesheet" href="https://fonts.googleapis.com/css2?family=Montserrat:wght@400;500;700&display=swap">
<style>
  :root {
    --backdrop: #d3d8d8;
    --card-stock: #ecedec;
    --ink: #24272b;
    --ink-soft: #3a3d41;
    --accent: #2aa6e4;
    --accent-deep: #0677ba;
    --edge: #0054aa;
    --emboss: #f6f7f6;
  }
  * { box-sizing: border-box; margin: 0; padding: 0; }
  html, body {
    width: 1200px; height: 881px; overflow: hidden;
    background: var(--backdrop);
    font-family: "Montserrat", sans-serif;
  }
  .stage { position: relative; width: 1200px; height: 881px; }
  .card {
    position: absolute; top: 292px;
    width: 520px; height: 297px;
    background: var(--card-stock);
    border-bottom: 5px solid var(--accent);
  }
  .card--front { left: 60px; }
  .card--back { left: 620px; border-bottom-color: var(--edge); }

  .brand-name {
    position: absolute; left: 140px; top: 34px;
    font-size: 30px; font-weight: 500; color: var(--ink);
    letter-spacing: 0.5px; white-space: nowrap;
  }
  .brand-dot {
    position: absolute; left: 116px; top: 45px;
    width: 14px; height: 14px; border-radius: 50%;
    background: var(--accent);
  }
  .abn {
    position: absolute; left: 86px; top: 112px;
    font-size: 14px; color: var(--ink-soft);
  }
  .contact {
    position: absolute; left: 40px; top: 188px;
    list-style: none; font-size: 14px; color: var(--ink-soft);
  }
  .contact li { display: flex; align-items: center; gap: 8px; line-height: 24px; }
  .contact svg { width: 13px; height: 13px; fill: var(--accent-deep); }

  .holder {
    position: absolute; right: 28px; top: 222px; text-align: right;
  }
  .holder-name { font-size: 20px; font-weight: 700; color: var(--accent); }
  .holder-role { font-size: 14px; color: var(--ink-soft); margin-top: 2px; }
  .holder-bar {
    position: absolute; right: 0; top: 226px;
    width: 14px; height: 44px; background: var(--accent);
  }

  .back-name {
    position: absolute; left: 0; right: 0; top: 118px;
    text-align: center; font-size: 40px; font-weight: 500;
    color: var(--emboss); letter-spacing: 1px;
  }
</style>
</head>
<body>
<main class="stage">
  <section class="card card--front" aria-label="Business card front">
    <span class="brand-dot"></span>
    <p class="brand-name">TBK Plumbing Services</p>
    <p class="abn">Company ABN - 73 215 904 386</p>
    <ul class="contact">
      <li>
        <svg viewBox="0 0 24 24" aria-hidden="true"><path d="M6.6 10.8a15.1 15.1 0 0 0 6.6 6.6l2.2-2.2a1 1 0 0 1 1-.25 11.4 11.4 0 0 0 3.6.57 1 1 0 0 1 1 1V20a1 1 0 0 1-1 1A17 17 0 0 1 3 4a1 1 0 0 1 1-1h3.5a1 1 0 0 1 1 1c0 1.25.2 2.45.57 3.57a1 1 0 0 1-.25 1z"/></svg>
        0431 286 517
      </li>
      <li>
        <svg viewBox="0 0 24 24" aria-hidden="true"><path d="M2 5h20v14H2zm2 2v.5l8 5 8-5V7zm0 2.8V17h16V9.8l-8 5z"/></svg>
        rowan@tbk-plumbing.com.au
      </li>
    </ul>
    <div class="holder">
      <p class="holder-name">Rowan Keddle</p>
      <p class="holder-role">Director</p>
    </div>
    <span class="holder-bar"></span>
  </section>

  <section class="card card--back" aria-label="Business card back">
    <p class="back-name">TBK Plumbing Services</p>
  </section>
</main>
</body>
</html>
```